Mesquite Power Source Sales Training

I need a job posting flyer for a hands on Sales Training positions in the electrical distribution market of Phoenix, Arizona. The flyer will be posted on college campuses to recruit new grads for my company. I would like to highlight the benefits of Professional Sales jobs such as a flexible schedule, some out of state travel for training, accelerating career path, and control of earnings based on performance. This is not an everyday sales position, it is professional, complex, and competitive. Applicants should have an entrepreneurial mindset as they will run their accounts as their own business. Mesquite Power Source sells construction electric material to customers in a large scale including electrical conduit, Wire, fittings, high tech lighting and building controls along with other green energy saving devices.
Applicants will send resumes to DaneR@MPSTempe.example

I have added some pictures that inspire me

Target Market(s)

New college graduates, any bachelors degree

Industry/Entity Type

Electrical Equipment

Font styles to use
Serif

Colors

Designer to choose colors to be used in the design.

Requirements
Must have
• Photos that help show what our industry does, most people are unaware of this industry
• Not wordy, short, get the point across, and where to apply
Nice to have
• creativity and simplicity
Should not have
• too many words

```html
<!DOCTYPE html>
<html lang="en">
<head>
<meta charset="utf-8">
<title>Mesquite Power Source – Sales Training Positions</title>
<link rel="stylesheet" href="https://fonts.googleapis.com/css2?family=Oswald:wght@500;600&family=Ubuntu:wght@300;500;700&family=PT+Sans:wght@400&display=swap">
<style>
  :root {
    --brand-red: #b3181f;
    --ink: #111111;
    --paper: #ffffff;
    --paper-shade: #eeeeee;
    --blueprint-glow: #5a9be6;
    --blueprint-light: #2f6fc4;
    --blueprint-mid: #1a4698;
    --blueprint-dark: #0c2456;
  }
  * { margin: 0; padding: 0; box-sizing: border-box; }
  html, body { width: 971px; height: 1200px; overflow: hidden; background: var(--paper); }
  .flyer {
    position: relative;
    width: 971px;
    height: 1200px;
    overflow: hidden;
    background: radial-gradient(ellipse at 40% 75%, var(--paper) 40%, var(--paper-shade) 100%);
    font-family: "Ubuntu", sans-serif;
    color: var(--ink);
  }
  .header-art { position: absolute; left: 0; top: 0; width: 971px; height: 720px; }
  .hiring-banner { position: absolute; left: 633px; top: 0; width: 310px; height: 275px; }
  .hiring-banner__text {
    position: absolute;
    left: 633px; top: 55px; width: 310px;
    text-align: center;
    font-family: "Oswald", sans-serif;
    font-weight: 600;
    font-size: 84px;
    line-height: 77px;
    color: var(--paper);
    letter-spacing: 2px;
    text-shadow: 0 3px 4px rgba(0,0,0,.45);
  }
  .role-title {
    position: absolute;
    left: 32px; top: 594px;
    font-family: "Oswald", sans-serif;
    font-weight: 500;
    font-size: 46px;
    line-height: 49px;
    color: var(--brand-red);
    text-transform: uppercase;
  }
  .benefits-tab {
    position: absolute; left: 0; top: 757px; width: 352px; height: 60px;
    filter: drop-shadow(3px 4px 4px rgba(0,0,0,.35));
  }
  .benefits-tab__label {
    position: absolute; left: 30px; top: 763px;
    font-family: "Ubuntu", sans-serif; font-weight: 300;
    font-size: 38px; line-height: 48px;
    color: var(--paper);
  }
  .benefit-list { position: absolute; left: 32px; top: 858px; list-style: none; }
  .benefit-list li {
    display: flex; align-items: center;
    font-size: 25px; line-height: 39px; font-weight: 500;
    white-space: nowrap;
  }
  .benefit-list svg { width: 22px; height: 22px; margin-right: 12px; flex: none; }
  .brand-name {
    position: absolute; left: 530px; top: 806px; width: 420px;
    display: flex; align-items: center; justify-content: center; gap: 14px;
    font-family: "Ubuntu", sans-serif; font-weight: 700;
    font-size: 31px; line-height: 40px;
    white-space: nowrap;
    color: var(--ink);
  }
  .brand-name__dot { width: 26px; height: 26px; border-radius: 50%; background: var(--brand-red); flex: none; }
  .company-blurb {
    position: absolute; left: 32px; top: 1041px; width: 915px;
    font-family: "PT Sans", sans-serif;
    font-size: 15.6px; line-height: 23px; color: var(--ink);
  }
  .apply-bar { position: absolute; left: 0; top: 1114px; width: 971px; height: 86px; }
  .apply-bar__prompt {
    position: absolute; left: 22px; top: 1114px; height: 78px;
    display: flex; align-items: center;
    font-weight: 700; font-size: 26px; color: var(--paper);
    white-space: nowrap;
  }
  .apply-bar__email {
    position: absolute; left: 545px; top: 1114px; height: 90px;
    display: flex; align-items: center; gap: 12px;
    font-weight: 700; font-size: 27px; color: var(--paper);
    white-space: nowrap;
  }
  .apply-bar__email svg { width: 30px; height: 30px; flex: none; }
</style>
</head>
<body>
<main class="flyer">
  <svg class="header-art" viewBox="0 0 971 720">
    <defs>
      <radialGradient id="blueprint-tone" cx="52%" cy="48%" r="68%">
        <stop offset="0" stop-color="var(--blueprint-glow)"/>
        <stop offset="0.35" stop-color="var(--blueprint-light)"/>
        <stop offset="0.7" stop-color="var(--blueprint-mid)"/>
        <stop offset="1" stop-color="var(--blueprint-dark)"/>
      </radialGradient>
      <linearGradient id="band-tone" x1="0" y1="0" x2="1" y2="0">
        <stop offset="0" stop-color="#2a2a2a"/>
        <stop offset="0.5" stop-color="#101010"/>
        <stop offset="1" stop-color="#2a2a2a"/>
      </linearGradient>
    </defs>
    <polygon role="img" aria-label="Blueprint wireframe of a high-rise tower under construction, seen from below" points="0,0 971,0 971,540 751,622 0,428" fill="url(#blueprint-tone)"/>
    <polygon points="0,428 751,622 971,540 971,558 751,642 0,452" fill="var(--brand-red)"/>
    <polygon points="0,452 751,642 971,558 971,565 751,650 0,460" fill="var(--paper)"/>
    <polygon points="0,460 751,650 971,565 971,630 751,712 0,521" fill="url(#band-tone)"/>
  </svg>

  <svg class="hiring-banner" viewBox="0 0 310 275">
    <polygon points="0,0 310,0 310,275 155,246 0,275" fill="var(--paper)"/>
    <polygon points="6,0 304,0 304,266 155,239 6,266" fill="var(--brand-red)"/>
  </svg>
  <h1 class="hiring-banner__text">WE'RE<br>HIRING</h1>

  <h2 class="role-title">Sales<br>Training<br>Positions</h2>

  <svg class="benefits-tab" viewBox="0 0 352 60">
    <polygon points="0,0 332,0 352,60 0,60" fill="var(--ink)"/>
  </svg>
  <h3 class="benefits-tab__label">BENEFITS</h3>

  <ul class="benefit-list">
    <li><svg viewBox="0 0 22 22"><circle cx="11" cy="11" r="11" fill="var(--ink)"/><path d="M6 11.5l3.3 3.3L16 8" stroke="#fff" stroke-width="2.4" fill="none"/></svg>Flexible schedule</li>
    <li><svg viewBox="0 0 22 22"><circle cx="11" cy="11" r="11" fill="var(--ink)"/><path d="M6 11.5l3.3 3.3L16 8" stroke="#fff" stroke-width="2.4" fill="none"/></svg>Some out of state travel for training</li>
    <li><svg viewBox="0 0 22 22"><circle cx="11" cy="11" r="11" fill="var(--ink)"/><path d="M6 11.5l3.3 3.3L16 8" stroke="#fff" stroke-width="2.4" fill="none"/></svg>Accelerating career path</li>
    <li><svg viewBox="0 0 22 22"><circle cx="11" cy="11" r="11" fill="var(--ink)"/><path d="M6 11.5l3.3 3.3L16 8" stroke="#fff" stroke-width="2.4" fill="none"/></svg>Control of earnings based on Performance</li>
  </ul>

  <div class="brand-name"><span class="brand-name__dot"></span><span>Mesquite Power Source</span></div>

  <p class="company-blurb">Mesquite Power Source sells construction electric material to customers in a large scale including: electrical conduit, wire, fittings, high tech lighting and building controls along with other green energy saving devices.</p>

  <svg class="apply-bar" viewBox="0 0 971 86" preserveAspectRatio="none">
    <defs>
      <linearGradient id="email-tone" x1="0" y1="0" x2="1" y2="0">
        <stop offset="0" stop-color="#0d0d0d"/>
        <stop offset="0.55" stop-color="#3a3a3a"/>
        <stop offset="1" stop-color="#0d0d0d"/>
      </linearGradient>
    </defs>
    <rect x="0" y="0" width="971" height="86" fill="url(#email-tone)"/>
    <polygon points="0,0 500,0 472,86 0,86" fill="var(--paper)"/>
    <polygon points="0,0 490,0 462,86 0,86" fill="var(--brand-red)"/>
  </svg>
  <p class="apply-bar__prompt">Applicants will send resumes to</p>
  <p class="apply-bar__email">
    <svg viewBox="0 0 30 30" aria-hidden="true"><circle cx="15" cy="15" r="14" fill="var(--brand-red)"/><rect x="8" y="10" width="14" height="10" fill="#fff"/><path d="M8 10l7 6 7-6" stroke="var(--brand-red)" stroke-width="1.6" fill="none"/></svg>
    DaneR@MPSTempe.example
  </p>
</main>
</body>
</html>
```